German Headhunter/ HR Consultancy needs Business Cards Design

We need a business Card Design for our Company in Stuttgart. We are specialized as Headhunter/ HR Consultancy in Placement of specialist and managers in permanent employment. Please refer to our business logo.

```html
<!DOCTYPE html>
<html lang="de">
<head>
<meta charset="utf-8">
<title>Kernwerk Personalberatung – Visitenkarte</title>
<link rel="stylesheet" href="https://fonts.googleapis.com/css2?family=Montserrat:wght@600;700&family=Arimo:wght@400&display=swap">
<style>
  :root {
    --brand-blue: #3853a7;
    --card-white: #ffffff;
    --text-grey: #666666;
    --rule-grey: #9a9a9a;
    --stage: #a3a3a3;
  }
  * { margin: 0; padding: 0; box-sizing: border-box; }
  html, body { width: 1200px; height: 1200px; overflow: hidden; }
  body { background: var(--stage); position: relative; font-family: "Arimo", Arial, sans-serif; }

  .card { position: absolute; top: 303px; width: 368px; height: 594px; }
  .card--front { left: 200px; background: var(--brand-blue); }
  .card--back { left: 599px; background: var(--card-white); }

  .wordmark { position: absolute; display: flex; align-items: center; gap: 14px; font-family: "Montserrat", sans-serif; font-weight: 700; }
  .wordmark__square { width: 30px; height: 30px; flex: none; }
  .wordmark__text { line-height: 1; }
  .wordmark__name { display: block; font-size: 33px; letter-spacing: 0.5px; }
  .wordmark__sub { display: block; font-size: 14.5px; margin-top: 6px; letter-spacing: 0.2px; }

  .card--front .wordmark { left: 36px; top: 478px; color: var(--card-white); }
  .card--front .wordmark__square { background: var(--card-white); }
  .card--back .wordmark { left: 34px; top: 126px; color: var(--brand-blue); }
  .card--back .wordmark__square { background: var(--brand-blue); }

  .contact { position: absolute; left: 0; top: 0; width: 100%; height: 100%; text-align: center; color: var(--text-grey); }
  .contact__name { position: absolute; top: 338px; width: 100%; font-family: "Montserrat", sans-serif; font-weight: 700; font-size: 23px; color: var(--brand-blue); }
  .contact__role { position: absolute; top: 366px; width: 100%; font-size: 15px; letter-spacing: 0.3px; }

  .icon-row { position: absolute; top: 395px; left: 0; width: 100%; display: flex; justify-content: center; align-items: center; gap: 4px; }
  .icon-row__rule { width: 52px; height: 1px; background: var(--rule-grey); margin: 0 4px; }
  .icon-row__icon { width: 25px; height: 25px; background: var(--brand-blue); border-radius: 3px; display: flex; align-items: center; justify-content: center; }

  .contact__lines { position: absolute; top: 431px; width: 100%; font-size: 16.5px; line-height: 22px; letter-spacing: 0.3px; }
  .contact__lines .accent { color: var(--brand-blue); }
  .contact__divider { position: absolute; top: 507px; left: 88px; width: 195px; height: 1px; background: var(--rule-grey); }
  .contact__address { position: absolute; top: 518px; width: 100%; font-size: 16.5px; line-height: 22px; letter-spacing: 0.3px; }
</style>
</head>
<body>

<section class="card card--front" aria-label="Vorderseite">
  <div class="wordmark">
    <span class="wordmark__square"></span>
    <span class="wordmark__text">
      <span class="wordmark__name">KERNWERK</span>
      <span class="wordmark__sub">PERSONALBERATUNG</span>
    </span>
  </div>
</section>

<section class="card card--back" aria-label="Rückseite">
  <div class="wordmark">
    <span class="wordmark__square"></span>
    <span class="wordmark__text">
      <span class="wordmark__name">KERNWERK</span>
      <span class="wordmark__sub">PERSONALBERATUNG</span>
    </span>
  </div>

  <div class="contact">
    <div class="contact__name">JONAS BECKER</div>
    <div class="contact__role">MANAGING DIRECTOR</div>

    <div class="icon-row">
      <span class="icon-row__rule"></span>
      <span class="icon-row__icon">
        <svg width="15" height="13" viewBox="0 0 15 13" aria-label="Telefon" role="img">
          <path d="M1 4 Q7.5 -1 14 4 L12 5.5 L10 4 L5 4 L3 5.5 Z" fill="#fff"/>
          <rect x="3" y="6" width="9" height="6" rx="1" fill="#fff"/>
        </svg>
      </span>
      <span class="icon-row__icon">
        <svg width="15" height="11" viewBox="0 0 15 11" aria-label="E-Mail" role="img">
          <rect x="0.75" y="0.75" width="13.5" height="9.5" fill="none" stroke="#fff" stroke-width="1.3"/>
          <path d="M1 1 L7.5 6 L14 1 M1 10 L5.5 5 M14 10 L9.5 5" fill="none" stroke="#fff" stroke-width="1.1"/>
        </svg>
      </span>
      <span class="icon-row__icon">
        <svg width="15" height="15" viewBox="0 0 15 15" aria-label="Web" role="img">
          <circle cx="7.5" cy="7.5" r="6.5" fill="none" stroke="#fff" stroke-width="1.4"/>
          <ellipse cx="7.5" cy="7.5" rx="2.8" ry="6.5" fill="none" stroke="#fff" stroke-width="1"/>
          <path d="M1 7.5 H14" stroke="#fff" stroke-width="1"/>
        </svg>
      </span>
      <span class="icon-row__rule"></span>
    </div>

    <div class="contact__lines">
      0711-482 930 5<br>
      info@kernwerk.de<br>
      www.<span class="accent">kernwerk-hr</span>.de
    </div>
    <div class="contact__divider"></div>
    <div class="contact__address">
      Lindenweg 27, 3. OG<br>
      70173 Stuttgart, DE
    </div>
  </div>
</section>

</body>
</html>
```